$5 Quest Website Required

I am looking for someone to develop a website akin to the simplicity of www.boxlantern.example with a video in the center or a tab that permits one to "Accept the Challenge."

Incorporates our logo and is used to promote our "$5 Quest Program."

Please see attachments, but we are igniting entrepreneurial spirit among our nation's youth through this interactive and intensive program!

There should be a way to navigate to other sections of the site including:

About
Why
Request $5 Quest Packet
Success Stories
Partners
Link to Norvik Holdings
Updates

Thanks to all in advance!

Looking forward to working with you!

Good feel of what we are looking for in terms of "feel"

http://www.thebrightripple.example/

Thank you,

RB

Please make note of this website, we are going for a feel that is akin to this and less modern and professional...more abstract and interactive...but of course include space for our video:

Colors, feel, imagery, is great. Keep your formats, but bring on the feel!

Thank you all for your hard work and patience.

Thank you all for your hard work thus far.

Meanwhile, please understand that the $5 Quest is young, youthful, full of challenge and vitality, it is a competition among students from high school and universities.  The websites you have delivered are too corporate, stale, and standard.  I'm looking for something that is fresh, different, like www.thebrightripple.example.

Symbols, cartoonish, but serious, down to business and save the world one $5 bill at a time.  The logo can be used as a theme...the colors, the feel.

Video space for explanation on the $5 Quest front and center.  With leaves, $ signs, colorful colors, etc.

Visual needs to be compelling to Join the Challenge! Although Norvik Holdings and the tree is a parent company; $5 Quest is separate and Norvik Holdings should only be mentioned as a link.

PixelHarbor.example in regard to simplicity; and www.thebrightripple.example in terms of style.

Thank you,

Raphael

Like the designs that have been submitted; we are almost there.

Target Market(s)

Professors, students, teachers, parents and NGO leaders who wish to use our program as a way to inspire leadership/entrepreneurship/fundraise for their causes.

Requirements
Must have
• Place for the video, front and center
Include logo
Forsight for blogging, message, etc.
Nice to have
• Plan "buckets" to include"
Explanation Video
Two pamphlets
Contract
FAQs
Website with Blog, voting, registration, video upload, etc.
Flyer perfected
Parable...symbol of our life
Photos
Stats included
Testimonials
Organizations that have used (TKWLM, North Brook Lodge, Marlowton High)
Sponsors (Open Lantern, Copperleaf Learningfield)
Photos from events

I understand this takes coding and such, but want you to be aware of the long term vision for it!

```html
<!DOCTYPE html>
<html lang="en">
<head>
<meta charset="utf-8">
<title>$5 Quest</title>
<link rel="stylesheet" href="https://fonts.googleapis.com/css2?family=Arimo:wght@400;700&family=Roboto+Condensed:wght@400;500&display=swap">
<style>
  :root {
    --green: #0b9444;
    --green-light: #2fb35c;
    --green-dark: #07753a;
    --lime: #dde437;
    --lime-dark: #c9d12a;
    --ink: #333333;
    --ink-soft: #4a4a4a;
    --nav-active: #1f3b2a;
    --white: #ffffff;
    --frame: #dcdcdc;
    --orange: #ff8a00;
    --orange-dark: #f06d00;
    --orange-text: #b35a00;
    --quote: #f0b91b;
  }
  * { box-sizing: border-box; margin: 0; padding: 0; }
  html, body { width: 1200px; height: 996px; overflow: hidden; }
  body {
    position: relative;
    font-family: "Arimo", Arial, sans-serif;
    color: var(--ink);
    background: var(--white);
  }
  .site-header { position: absolute; top: 0; left: 0; width: 1200px; height: 216px; background: var(--white); }
  .utility-bar { position: absolute; top: 4px; right: 34px; display: flex; align-items: center; }
  .utility-link {
    font-family: "Roboto Condensed", sans-serif; font-weight: 500; font-size: 16px;
    color: #111; text-decoration: none; padding: 0 13px; letter-spacing: 0.5px;
  }
  .utility-link.signin { background: linear-gradient(90deg, #e8e8e8, #fff 30%); padding: 3px 14px 3px 20px; }
  .language-button {
    margin-left: 8px; background: var(--green); color: var(--white); border-radius: 3px;
    font-family: "Roboto Condensed", sans-serif; font-weight: 500; font-size: 14px;
    height: 29px; width: 105px; display: flex; align-items: center; justify-content: space-between;
    padding: 0 10px 0 8px;
  }
  .brand {
    position: absolute; left: 300px; top: 40px; width: 600px; height: 130px;
    display: flex; align-items: center; justify-content: center;
  }
  .brand-name {
    font-family: "Arimo", sans-serif; font-weight: 700; font-size: 64px;
    color: var(--green); letter-spacing: 0.5px;
  }

  .main-nav {
    position: absolute; top: 216px; left: 0; width: 1200px; height: 60px;
    background: var(--green); border-top: 4px solid var(--green-dark); border-bottom: 4px solid var(--green-light);
    display: flex; justify-content: center; align-items: center;
  }
  .main-nav a {
    font-family: "Roboto Condensed", sans-serif; font-weight: 500; font-size: 21px; letter-spacing: 0.6px;
    color: var(--white); text-decoration: none; display: flex; align-items: center;
  }
  .main-nav a + a::before {
    content: ""; width: 6px; height: 6px; border-radius: 50%; background: var(--green-light);
    margin: 0 24px;
  }
  .main-nav a.active { color: var(--nav-active); }

  .content { position: absolute; top: 276px; left: 0; width: 1200px; height: 720px; background: var(--lime); }

  .welcome { position: absolute; left: 24px; top: 52px; width: 314px; }
  .section-title {
    font-family: "Arimo", sans-serif; font-size: 21px; font-weight: 400; color: var(--ink-soft);
    padding-bottom: 8px; border-bottom: 1px dotted #6b6b2a; letter-spacing: 0.3px;
  }
  .section-title .accent { color: var(--green); }
  .welcome p { font-size: 14.5px; line-height: 21.6px; text-align: justify; color: var(--ink); margin-top: 8px; }
  .welcome p:first-of-type { margin-top: 20px; }

  .video-frame {
    position: absolute; left: 394px; top: 22px; width: 534px; height: 444px;
    background: var(--white); border-radius: 8px; padding: 8px;
    box-shadow: 0 36px 28px -26px rgba(60,60,20,0.55);
  }
  .video-inner {
    width: 100%; height: 100%; border: 7px solid var(--frame); border-radius: 4px;
    background: var(--white); position: relative;
  }
  .play-icon { position: absolute; left: 172px; top: 79px; }
  .watch-label {
    position: absolute; left: 0; right: 0; top: 300px; text-align: center;
    font-family: "Roboto Condensed", sans-serif; font-weight: 500; font-size: 31px; color: #222;
  }

  .testimonials { position: absolute; left: 974px; top: 52px; width: 200px; }
  .testimonials .section-title { text-align: right; color: #111; }
  .quote { position: relative; margin-top: 16px; padding: 0 18px 0 8px; }
  .quote::before {
    content: "\201C"; position: absolute; left: -24px; top: -20px;
    font-family: Georgia, serif; font-size: 110px; line-height: 1; color: var(--quote); opacity: 0.75;
  }
  .quote p { position: relative; font-size: 14.5px; line-height: 19.2px; text-align: justify; color: var(--ink); }
  .quote cite { display: block; text-align: right; font-style: normal; font-size: 14px; color: #111; margin: 10px -18px 0 0; }
  .quote + .quote { margin-top: 30px; }

  .cta { position: absolute; left: 288px; top: 512px; width: 708px; height: 65px; }
  .cta-line { position: absolute; top: 32px; height: 0; border-top: 2px dashed var(--green); }
  .cta-line.left { left: 0; width: 156px; }
  .cta-line.right { right: 0; width: 156px; }
  .cta-button { position: absolute; left: 156px; top: 0; width: 396px; height: 65px; }
  .cta-label {
    position: absolute; left: 0; right: 0; top: 18px; text-align: center;
    font-family: "Roboto Condensed", sans-serif; font-size: 25px; color: var(--orange-text);
  }

  .site-footer { position: absolute; left: 24px; top: 626px; width: 1152px; border-top: 1px dotted #a9ad2a; }
  .footer-brand {
    position: absolute; left: 5px; top: 8px; width: 168px; height: 72px;
    border: 1px solid var(--lime-dark); display: flex; align-items: center; justify-content: center;
    font-size: 22px; font-weight: 700; color: var(--green);
  }
  .footer-links { position: absolute; right: 12px; top: 24px; display: flex; gap: 19px; }
  .footer-links a { font-size: 13px; color: var(--ink); text-decoration: none; }
  .copyright { position: absolute; right: 12px; top: 50px; font-size: 13px; color: var(--ink); }
</style>
</head>
<body>
  <header class="site-header">
    <div class="utility-bar">
      <a class="utility-link" href="#">FAQ</a>
      <a class="utility-link signin" href="#">SIGNIN</a>
      <div class="language-button"><span>LANGUAGE</span>
        <svg width="12" height="10" viewBox="0 0 12 10" aria-hidden="true"><polygon points="0,0 12,0 6,10" fill="#fff"/></svg>
      </div>
    </div>
    <div class="brand">
      <span class="brand-name">$5 Quest</span>
    </div>
  </header>

  <nav class="main-nav">
    <a class="active" href="#">HOME</a>
    <a href="#">ABOUT US</a>
    <a href="#">WHY WE ARE?</a>
    <a href="#">SUCCESS STORIES</a>
    <a href="#">PARTNERS</a>
    <a href="#">NORVIK HOLDINGS</a>
  </nav>

  <main class="content">
    <section class="welcome">
      <h2 class="section-title">WELCOME TO <span class="accent">$5 QUEST</span></h2>
      <p>Lorem ipsum dolor sit amet, consectetur adipiscing elit. Curabitur eu nisl odio. Cras egestas turpis in mi feugiat vel tincidunt arcu accumsan. Phasellus non posuere eros. Aenean consectetur.</p>
      <p>sapien in elit luctus ac posuere purus placerat. Aliquam turpis lorem,.</p>
      <p>Donec fermentum sodales erat, quis consequat nisi ornare eget. Duis volutpat justo ut ante imperdiet feugiat. fermentum sodales erat, quis consequat nisi ornare eget. Duis volutpat justo ut ante imperdiet feugiat.</p>
      <p>sapien in elit luctus ac posuere purus placerat. Aliquam turpis lorem,.</p>
    </section>

    <section class="video-frame">
      <div class="video-inner">
        <svg class="play-icon" width="174" height="174" viewBox="0 0 174 174" role="img" aria-label="Play video">
          <defs>
            <linearGradient id="playFill" x1="0" y1="0" x2="0" y2="1">
              <stop offset="0" stop-color="#111"/>
              <stop offset="1" stop-color="#3a3a3a"/>
            </linearGradient>
          </defs>
          <circle cx="87" cy="87" r="87" fill="url(#playFill)"/>
          <polygon points="70,54 70,120 116,87" fill="#d9d9d9"/>
        </svg>
        <div class="watch-label">WATCH VIDEO</div>
      </div>
    </section>

    <aside class="testimonials">
      <h2 class="section-title"><span class="accent">Client</span> Testimonials</h2>
      <blockquote class="quote">
        <p>Lorem ipsum dolor sit amsectetur adipiscing elit. Curabitur eu nisl odio. dolor sit amsectetur u nisl odio.</p>
        <cite>- LOREM IPSUM</cite>
      </blockquote>
      <blockquote class="quote">
        <p>Lorem ipsum dolor sit amsectetur adipiscing elit. Curabitur eu nisl odio. dolor sit amsectetur u nisl odio.</p>
        <cite>- LOREM IPSUM</cite>
      </blockquote>
    </aside>

    <div class="cta">
      <span class="cta-line left"></span>
      <span class="cta-line right"></span>
      <a class="cta-button" href="#">
        <svg width="396" height="65" viewBox="0 0 396 65" aria-hidden="true">
          <polygon points="0,0 396,0 380,32 396,65 0,65 16,32" fill="var(--orange-dark)"/>
          <polygon points="10,5 386,5 372,32 386,60 10,60 24,32" fill="var(--orange)"/>
        </svg>
        <span class="cta-label">ACCEPT THE CHALLENGE</span>
      </a>
    </div>

    <footer class="site-footer">
      <div class="footer-brand"><span>$5 Quest</span></div>
      <nav class="footer-links">
        <a href="#">Home</a>
        <a href="#">About Us</a>
        <a href="#">Success Stories</a>
        <a href="#">Partners</a>
        <a href="#">Norvik Holdings</a>
        <a href="#">Terms</a>
        <a href="#">Privacy Policy</a>
      </nav>
      <p class="copyright">All Rights reserved @ $5quest</p>
    </footer>
  </main>
</body>
</html>
```